Menu Design Project

My Restaurant is called The Platter Corner, it's fast food restaurant serves Gyro, Wings, Subs, Fried Seafood and chicken tenders. I'm looking for a menu design to fit the fast food category and have some photos of the food on the front page as well inside the menu. I will attached some photos and you can add any other photo related to the menu from the web.

Industry/Entity Type

Restaurant

```html
<!DOCTYPE html>
<html lang="en">
<head>
<meta charset="utf-8">
<title>The Platter Corner – Menu</title>
<link rel="stylesheet" href="https://fonts.googleapis.com/css2?family=Montserrat:wght@400;500;600;700&family=Oswald:wght@300;500;600&family=Dancing+Script:wght@600&display=swap">
<style>
  :root{
    --red:#e3161b;
    --red-pale:#f4b4b6;
    --ink:#1d1d1d;
    --muted:#555;
    --paper:#ffffff;
    --stage:#e6e7e9;
    --photo-warm:#c8692e;
    --photo-brown:#8a5a33;
    --photo-green:#7a9a4a;
    --map-grey:#d9dadc;
  }
  *{box-sizing:border-box;margin:0;padding:0}
  html,body{width:1200px;height:770px;overflow:hidden}
  body{background:var(--stage);font-family:"Montserrat",Arial,sans-serif;color:var(--ink);position:relative}

  .sheet{position:absolute;top:50px;width:570px}
  .sheet--outside{left:20px}
  .sheet--inside{left:610px}
  .panel{position:relative;width:570px;height:335px;background:var(--paper);overflow:hidden;box-shadow:0 2px 6px rgba(0,0,0,.18)}
  .panel + .panel{margin-top:1px}
  .panel--back{transform:rotate(180deg)}
  .frame{position:absolute;inset:8px;border:2px solid var(--red);pointer-events:none}

  .corner{position:absolute;width:0;height:0}
  .abs{position:absolute}

  .tag{position:absolute;height:15px;background:var(--red);color:#fff;font-weight:700;font-size:10px;white-space:nowrap;
       font-variant:small-caps;letter-spacing:.06em;line-height:15px;padding-left:20px;border-radius:2px}
  .tag::before{content:"";position:absolute;left:6px;top:3px;width:9px;height:9px;border:1.5px solid #fff;border-radius:50%;box-sizing:border-box}
  .tag--right{padding-left:14px}
  .tag--right::before{left:auto;right:8px}
  .tag small{font-size:8px;letter-spacing:.03em}

  .price-list{position:absolute;list-style:none;font-size:9.5px;line-height:14px}
  .price-list li{display:flex;justify-content:space-between;white-space:nowrap;gap:8px}
  .price-list .note{color:var(--red);font-size:9.5px}
  .price-list .red{color:var(--red);font-weight:700}

  .photo{position:absolute;border-radius:10px}
  .mark{display:inline-block;border-radius:50%;background:var(--red)}

  /* cover */
  .brand-name{position:absolute;left:0;right:0;text-align:center;font-weight:700;font-size:15px}
  .headline{position:absolute;left:0;right:0;text-align:center;font-family:"Oswald",sans-serif;font-weight:500;font-size:27px;color:var(--red)}
  .hours{position:absolute;left:0;right:0;text-align:center;font-family:"Oswald",sans-serif;font-weight:300;font-size:16px}
  .hours strong{font-weight:600;color:var(--red);font-size:17px}
  .contact-band{position:absolute;left:8px;right:8px;bottom:8px;height:24px;background:var(--red);color:#fff;
       display:flex;align-items:center;gap:8px;padding:0 14px;font-size:11.5px;letter-spacing:.02em}
  .contact-band .phone{margin-left:auto;display:flex;align-items:center;gap:6px;font-size:12.5px}
  .contact-band svg,.address-line svg{flex:none}

  /* back */
  .slogan-band{position:absolute;left:8px;right:8px;top:8px;height:30px;background:var(--red);color:#fff;
       font-family:"Dancing Script",cursive;font-size:18px;line-height:30px;padding-left:40px}
  .drinks-list{position:absolute;list-style:none;font-size:9.5px;line-height:13px;font-style:italic;white-space:nowrap}
  .call{position:absolute;font-size:9px;text-align:center}
  .call strong{display:block;color:var(--red);font-size:11px;font-style:italic}
  .back-hours{position:absolute;font-size:10px;text-align:center}
  .back-hours strong{display:block;color:var(--red);font-size:11px;font-family:"Oswald",sans-serif;font-weight:500}
  .address-line{position:absolute;left:22px;right:22px;top:284px;border-top:1.5px solid var(--red);padding-top:8px;
       display:flex;align-items:center;gap:8px;font-size:10px}

  /* inside */
  .menu-title{position:absolute;left:0;right:0;text-align:center;color:var(--red);font-weight:700;font-size:12.5px}
  .cheese-note{position:absolute;color:var(--red);font-size:6.5px;white-space:nowrap}
</style>
</head>
<body>

<section class="sheet sheet--outside">

  <article class="panel panel--back">
    <div class="slogan-band">Good Food, Good Mood</div>
    <div class="corner" style="left:10px;top:38px;border-top:46px solid var(--red-pale);border-right:90px solid transparent"></div>

    <div class="tag" style="left:72px;top:56px;width:96px">Drinks</div>
    <ul class="drinks-list" style="left:78px;top:76px">
      <li>Cola, Diet Cola,</li>
      <li>Lemon-Lime, Sports Drink,</li>
      <li>Orange Soda,</li>
      <li>Strawberry Soda,</li>
      <li>Pepper Soda and more.</li>
    </ul>
    <div class="photo" role="img" aria-label="Photo of assorted soda cans" style="left:220px;top:58px;width:100px;height:95px;background:linear-gradient(135deg,#c92a2a,#3a8f3a 55%,#e58a1f)"></div>

    <span class="mark abs" style="left:142px;top:160px;width:24px;height:24px"></span>
    <p class="call" style="left:60px;top:192px;width:190px">Call Us for Pick Up orders or Catering<strong>713-555-0148</strong></p>

    <div class="photo" role="img" aria-label="Street map showing the restaurant location" style="left:332px;top:58px;width:223px;height:128px;border:2px solid #bbb;background:var(--map-grey)"></div>

    <p class="back-hours" style="left:320px;top:222px;width:170px">Hours of operation:<strong>Monday to Sunday 11am-9pm</strong></p>
    <div class="corner" style="right:10px;top:222px;border-bottom:52px solid var(--red-pale);border-left:100px solid transparent"></div>

    <div class="address-line">
      <svg width="10" height="10" viewBox="0 0 10 10"><circle cx="5" cy="5" r="4" fill="none" stroke="#e3161b" stroke-width="1.5"/><circle cx="5" cy="5" r="1.5" fill="#e3161b"/></svg>
      <span>4210 Harbor Crest Ave, Houston, TX 77021</span>
      <svg width="10" height="10" viewBox="0 0 10 10"><circle cx="5" cy="5" r="4" fill="none" stroke="#e3161b" stroke-width="1.2"/><path d="M3.5 3.2l1 1-.5.6 1.2 1.2.6-.5 1 1-.7.7c-1.5-.3-2.6-1.4-3-3z" fill="#e3161b"/></svg>
      <span>713-555-0148</span>
    </div>
    <div class="frame"></div>
  </article>

  <article class="panel panel--cover">
    <div class="corner" style="right:10px;top:10px;border-top:62px solid var(--red-pale);border-left:135px solid transparent"></div>
    <div class="corner" style="left:10px;bottom:32px;border-bottom:70px solid var(--red-pale);border-right:62px solid transparent"></div>

    <span class="mark abs" style="left:269px;top:18px;width:32px;height:32px"></span>
    <h1 class="brand-name" style="top:56px">The Platter Corner</h1>
    <h2 class="headline" style="top:76px">The Platter Corner Restaurant</h2>

    <div class="photo" role="img" aria-label="Photo of glazed chicken wings" style="left:45px;top:132px;width:120px;height:88px;background:radial-gradient(circle at 50% 45%,#d97a3a,var(--photo-brown))"></div>
    <div class="photo" role="img" aria-label="Photo of a cheeseburger" style="left:222px;top:130px;width:125px;height:90px;background:linear-gradient(180deg,#d59a4d 0 35%,var(--photo-green) 35% 45%,#6b3a22 45% 70%,#d59a4d 70%)"></div>
    <div class="photo" role="img" aria-label="Photo of a gyro wrap with meat and vegetables" style="left:395px;top:126px;width:140px;height:96px;background:linear-gradient(135deg,#efe0c0,var(--photo-brown) 55%,var(--photo-green))"></div>

    <p class="hours" style="top:242px">Hours of operation: <strong>Monday to Sunday 11am-9pm</strong></p>

    <div class="contact-band">
      <svg width="11" height="11" viewBox="0 0 10 10"><circle cx="5" cy="5" r="4" fill="none" stroke="#fff" stroke-width="1.4"/><circle cx="5" cy="5" r="1.5" fill="#fff"/></svg>
      <span>4210 Harbor Crest Ave, Houston, TX 77021</span>
      <span class="phone">
        <svg width="11" height="11" viewBox="0 0 10 10"><circle cx="5" cy="5" r="4" fill="none" stroke="#fff" stroke-width="1.2"/><path d="M3.5 3.2l1 1-.5.6 1.2 1.2.6-.5 1 1-.7.7c-1.5-.3-2.6-1.4-3-3z" fill="#fff"/></svg>
        713-555-0148
      </span>
    </div>
    <div class="frame"></div>
  </article>
</section>

<section class="sheet sheet--inside">

  <article class="panel panel--mains">
    <div class="corner" style="left:10px;top:10px;border-top:62px solid var(--red-pale);border-right:72px solid transparent"></div>
    <div class="corner" style="right:10px;top:10px;border-top:62px solid var(--red-pale);border-left:105px solid transparent"></div>

    <span class="mark abs" style="left:274px;top:18px;width:22px;height:22px"></span>
    <h1 class="menu-title" style="top:48px">The Platter Corner Menu</h1>

    <div class="tag" style="left:20px;top:68px;width:105px">Chicken</div>
    <ul class="price-list" style="left:32px;top:88px;width:180px">
      <li><span>10 Large Wings</span><span>$8.99</span></li>
      <li><span>20 Large Wings</span><span>$16.99</span></li>
      <li><span>30 Large Wings</span><span>$23.99</span></li>
      <li><span>50 Large Wings</span><span>$39.99</span></li>
      <li><span>½ lb. Chicken Strips</span><span>$5.49</span></li>
      <li><span>1lb. Chicken Strips</span><span>$7.99</span></li>
      <li><span>½ lb. Gizzards</span><span>$5.49</span></li>
      <li><span>1lb. Gizzards</span><span>$7.99</span></li>
    </ul>

    <div class="tag" style="left:20px;top:208px;width:105px">Seafood</div>
    <ul class="price-list" style="left:40px;top:228px;width:172px">
      <li><span>½ lb. Shrimp</span><span>$7.99</span></li>
      <li><span>1lb. Shrimp</span><span>$13.99</span></li>
      <li><span>½ lb. Fish</span><span>$6.99</span></li>
      <li><span>1lb. Fish</span><span>$12.99</span></li>
    </ul>

    <div class="tag tag--right" style="right:20px;top:70px;width:150px">Fresh Salad</div>
    <ul class="price-list" style="left:258px;top:90px;width:255px">
      <li><span>Caesar Salad</span><span>$4.95</span></li>
      <li><span>Gyro Salad</span><span>$5.95</span></li>
      <li><span>Shrimp Caesar Salad</span><span>$6.25</span></li>
      <li><span>Greek Salad</span><span>$5.95</span></li>
    </ul>

    <div class="tag tag--right" style="right:20px;top:156px;width:150px">Gyro &amp; Subs</div>
    <ul class="price-list" style="left:258px;top:176px;width:290px">
      <li><span>Gyro (Original or Chicken)</span><span>$6.99</span></li>
      <li><span>¼ lb. Black Angus Burger</span><span>$3.99</span></li>
      <li><span>Buffalo Chicken Sandwich</span><span>$5.99</span></li>
      <li><span class="note">YOUR CHOICE OF 6" OR FOOTLONG SUBS</span></li>
      <li><span>Po Boy Shrimp</span><span>$7.55-$9.25</span></li>
      <li><span>Philly (Steak or Chicken)</span><span>$6.75-$8.99</span></li>
      <li><span>Fish</span><span>$6.75-$8.99</span></li>
      <li><span>Turkey &amp; Cheese</span><span>$6.49-$7.95</span></li>
    </ul>
    <div class="frame"></div>
  </article>

  <article class="panel panel--sides">
    <div class="tag" style="left:18px;top:14px;width:100px">Sides</div>
    <ul class="price-list" style="left:28px;top:34px;width:190px">
      <li><span>French Fries</span><span>$2.79</span></li>
      <li><span>Cajun Fries</span><span>$3.99</span></li>
      <li><span>Onion Rings</span><span>$4.99</span></li>
      <li><span>5 Jalapeno Poppers</span><span>$4.99</span></li>
      <li><span>Fried Okra</span><span>$4.99</span></li>
      <li><span>Fried Mushroom</span><span>$5.49</span></li>
      <li><span>5 Mozzarella Sticks</span><span>$5.49</span></li>
    </ul>

    <div class="tag" style="left:295px;top:22px;width:257px">Combos <small>includes 16oz soft drink!</small></div>
    <ul class="price-list" style="left:250px;top:42px;width:232px">
      <li><span>½ lb. Fish &amp; Fries</span><span>$9.99</span></li>
      <li><span>½ lb. Shrimp &amp; Fries</span><span>$10.99</span></li>
      <li><span>6" Philly (Steak or Chicken) &amp; Fries</span><span>$9.99</span></li>
      <li><span>Gyro (Original, Chicken or Fish) &amp;Fries</span><span>$9.49</span></li>
      <li><span>5 Wings &amp; Fries</span><span>$9.49</span></li>
      <li><span>½ lb. Gizzards &amp; Fries</span><span>$7.99</span></li>
      <li><span>¼ lb. Black Angus Burger &amp; Fries</span><span>$6.99</span></li>
      <li><span>5 Wings &amp; Gizzards</span><span>$11.49</span></li>
      <li><span>½ lb. Chicken Strips &amp; Fries</span><span>$7.99</span></li>
    </ul>
    <span class="cheese-note" style="left:490px;top:127px">*CHEESE EXTRA</span>

    <div class="tag" style="left:235px;top:180px;width:120px">Kids Meal</div>
    <ul class="price-list" style="left:176px;top:202px;width:276px">
      <li><span>Chicken Nuggets 4pc with small drink and fries</span><span class="red">$4.95</span></li>
      <li><span>Chicken Strips 2pc with small drink and fries</span><span class="red">$4.95</span></li>
      <li><span style="margin-left:70px">Mac &amp; Cheese</span><span class="red" style="margin-right:70px">$3.95</span></li>
    </ul>

    <div class="photo" role="img" aria-label="Photo of a soft drink, fries, burger and chicken nuggets" style="left:20px;top:175px;width:150px;height:120px;background:linear-gradient(135deg,#c92a2a 0 30%,#e8b84a 30% 60%,var(--photo-warm))"></div>
    <div class="photo" role="img" aria-label="Photo of fries, chicken tenders and a soft drink cup" style="left:410px;top:248px;width:145px;height:76px;background:linear-gradient(135deg,#f2c54b,var(--photo-warm) 60%,#c92a2a)"></div>
    <div class="frame"></div>
  </article>
</section>

</body>
</html>
```